Community-based social network needs a new landing page

We need a landing page for a local social network in Singapore called "LaneKindred.sg". It is a website that help neighbours to connect with each other for mutual benefits such as providing professional/non-professional services, sharing items, and neighbourly help, etc.

There is an existing website but we want to completely revamp it. It is most important that the new landing page communicates that the neighbourhood has skills and services for people to discover.

The final design of the landing page should be modern, and communicates a sense of community and vibrancy. As a matter of priority, more real estate should be accorded to the neighbours providing services elements.

We have drafted 2 reference sites that communicates the key ideas/user propositions for your easy reference:
http://tarvelquin8.example-sites.com/lanekindred
http://tarvelquin8.example-sites.com/lanekindred2

As long as the key ideas/user propositions are kept to, we are open to any design proposals. I.e. you do not have to follow the design layout of the reference sites

Target Market(s)

Our target market is primarily the Singapore community, includes all genders, education levels and occupations, aged between 17-45 years old.

In the file uploaded, you will find pictures of Singapore neighbourhoods and people of local ethnicities. Please use them, but you may arrange and add further filters to better enhance them

Industry/Entity Type

Real Estate

Requirements
Nice to have
• Landing page could be similar to that of www.gatherloft.com, not just at the top, but also the way the other categories are presented at the bottom.

```html
<!DOCTYPE html>
<html lang="en">
<head>
<meta charset="utf-8">
<title>LaneKindred.sg — Meet People in Singapore</title>
<link rel="stylesheet" href="https://fonts.googleapis.com/css2?family=Crimson+Text:wght@400;600&family=Ubuntu:wght@400;500&display=swap">
<style>
:root{
  --white:#ffffff;
  --ink:#222222;
  --muted:#666666;
  --line:#e3e3e3;
  --red:#d5203a;
  --red-btn:#c9252d;
  --navy:#1d3a66;
  --green:#6a9b1e;
  --lavender:#8f95c8;
  --band:#d6e8f7;
  --footer:#202020;
  --yellow:#f6c000;
  --blue:#3b5998;
  --hero-dark:#2e2f31;
  --hero-mid:#6a6b6d;
}
*{box-sizing:border-box;margin:0;padding:0}
html,body{width:1141px;height:1200px;overflow:hidden;background:var(--white)}
body{position:relative;font-family:"Ubuntu",sans-serif;color:var(--ink)}
.abs{position:absolute}

/* header */
.site-header{position:absolute;left:0;top:0;width:1141px;height:81px;background:var(--white);border-bottom:1px solid #bbb}
.brand{left:133px;top:22px;display:flex;align-items:center;gap:8px;font-family:"Ubuntu",sans-serif;font-weight:500;font-size:27px;color:#4a4a4a;letter-spacing:-0.5px}
.brand-mark{width:14px;height:14px;background:var(--red)}
.login-label{font-family:"Crimson Text",serif;font-size:13px;color:#111}
.login-input{height:18px;width:173px;border:1px solid #bdbdbd;border-radius:2px;background:linear-gradient(#dadada,#f2f2f2)}
.login-note{font-family:"Crimson Text",serif;font-size:11px;color:#111}
.remember-box{width:8px;height:8px;background:#5a6a8a;display:inline-block;margin-right:7px}
.btn-login{left:868px;top:28px;width:57px;height:17px;background:var(--yellow);border-radius:2px;font-size:12px;text-align:center;line-height:17px;color:#222}
.or{left:939px;top:32px;font-family:"Crimson Text",serif;font-size:12px;color:#4aa3df}
.btn-connect{left:967px;top:27px;width:70px;height:20px;background:var(--blue);border-radius:2px;color:var(--white);font-size:11px;line-height:20px;display:flex;align-items:center;gap:6px;padding-left:5px}
.btn-connect i{width:10px;height:10px;background:var(--white);display:block}

/* hero */
.hero{left:0;top:81px;width:1141px;height:529px;background:linear-gradient(90deg,#4d4e50 0%,#8a8b8d 45%,#5c5d5f 75%,var(--hero-dark) 100%);overflow:hidden}
.hero-person{left:330px;top:20px;width:600px;height:509px;background:radial-gradient(ellipse at 50% 30%,#caa894 0%,#9b8a82 40%,#7d7f86 70%,rgba(90,90,95,0) 100%)}
.collage-photo{position:absolute;border:3px solid #d9dde3;background:linear-gradient(#b7b2ac,#7f7a76)}
.engineer{left:136px;top:437px;color:var(--white)}
.engineer b{font-size:15px;font-weight:500;display:block}
.engineer span{font-size:10px;display:flex;align-items:center;gap:4px;margin-top:2px}
.hero-title{right:105px;top:55px;text-align:right;font-family:"Crimson Text",serif;font-size:60px;line-height:57px;color:var(--white);letter-spacing:1px}
.hero-rule{left:782px;top:231px;width:254px;border-top:2px dashed rgba(255,255,255,.85)}
.hero-sub{right:105px;top:251px;text-align:right;font-family:"Crimson Text",serif;font-size:18px;line-height:21px;letter-spacing:1.2px;color:#f0f0f0}
.btn-try{left:914px;top:350px;width:122px;height:27px;background:var(--red-btn);border-radius:5px;color:var(--white);font-size:13px;text-align:center;line-height:27px}

/* features */
.feature{top:610px;height:198px;width:323px;padding:36px 27px 0 28px}
.feature + .feature{border-left:1px solid #ececec}
.feature-head{display:flex;align-items:center;gap:12px;height:40px;border-bottom:1px solid var(--line);padding-bottom:6px;margin-bottom:14px}
.feature-head h2{font-weight:400;font-size:21px;color:var(--red);line-height:22px}
.feature p{font-size:12.5px;line-height:19px;color:var(--muted)}
.feature a{display:inline-block;margin-top:14px;font-size:12px;font-style:italic;color:#333;text-decoration:underline}

/* band */
.band{left:0;top:808px;width:1141px;height:328px;background:linear-gradient(var(--band),#e6f1fb)}
.band-title{font-size:23px;font-weight:500;letter-spacing:-0.3px}
.quick-box{left:124px;top:865px;width:282px;height:233px;background:var(--white);border:3px solid #c5d3e0;padding:22px 30px 0 12px}
.post{display:flex;gap:8px;margin-bottom:18px}
.post-thumb{width:52px;height:52px;flex:none;border-radius:3px}
.post h3{font-weight:400;font-size:12.5px;border-bottom:1px dotted #aaa;padding-bottom:5px;margin-bottom:5px}
.post p{font-size:11px;line-height:14px;color:#555}
.post-meta{display:flex;justify-content:space-between;font-size:10.5px;color:#999;margin-top:2px}
.scrollbar{left:389px;top:878px;width:10px;height:210px}
.member{position:absolute;width:62px;height:62px;border:1px solid #9fb3c4}
.lorem-head{left:431px;top:1034px;font-size:19px;line-height:23px;font-weight:500;color:var(--lavender)}
.show-all{left:431px;top:1087px;font-size:11px;text-decoration:underline;color:#333}
.signup{left:735px;top:864px;width:285px;height:240px;background:#eef5fc;border:3px solid #c5d6e8;padding:0 14px}
.signup h3{font-weight:400;font-size:15px;letter-spacing:1.5px;padding:11px 6px 10px;border-bottom:1px solid #aaa}
.signup-input{height:27px;margin:19px 10px 0;border:1px solid #c9c9c9;background:var(--white);font-size:14px;color:#555;padding:4px 16px;letter-spacing:1px}
.signup-input + .signup-input{margin-top:11px}
.signup-row{display:flex;justify-content:space-between;align-items:center;margin:11px 10px 0}
.btn-next{width:73px;height:29px;background:linear-gradient(#f3f3f3,#d3d3d3);border:1px solid #bbb;font-size:15px;letter-spacing:1px;color:#555;text-align:center;line-height:27px}
.agree{font-size:11px;color:#333;display:flex;align-items:center;gap:8px;margin-right:40px}
.agree i{width:12px;height:12px;border:1px solid #4a6fa5;background:var(--white);display:block}
.signup-links{margin:26px 8px 0;font-size:9.5px;line-height:19px;letter-spacing:1px;color:#666}

/* footer */
.site-footer{left:0;top:1136px;width:1141px;height:64px;background:var(--footer);color:var(--white);font-size:12px}
.share-btn{position:absolute;top:22px;width:40px;height:16px;background:#eef2f8;border:1px solid #8aa0c0;color:#335;font-size:9px;text-align:center;line-height:14px;border-radius:2px}
</style>
</head>
<body>

<header class="site-header">
  <div class="abs brand"><span>LaneKindred.sg</span><span class="brand-mark"></span></div>
  <div class="abs login-label" style="left:504px;top:9px">Username or Email</div>
  <div class="abs login-input" style="left:502px;top:27px"></div>
  <div class="abs login-note" style="left:505px;top:47px"><span class="remember-box"></span>Remember me logged in</div>
  <div class="abs login-label" style="left:687px;top:9px">Password</div>
  <div class="abs login-input" style="left:684px;top:27px"></div>
  <div class="abs login-note" style="left:686px;top:47px">Forgotten your password?</div>
  <div class="abs btn-login">Login</div>
  <div class="abs or">OR</div>
  <div class="abs btn-connect"><i></i>Connect</div>
</header>

<section class="abs hero">
  <div class="abs hero-person" role="img" aria-label="Portrait of a young woman smiling thoughtfully, finger on her chin, blurred city behind"></div>
  <svg class="abs" style="left:120px;top:30px" width="320" height="450" aria-hidden="true">
    <g fill="none" stroke="#e8e8e8" stroke-width="2" stroke-dasharray="6 5">
      <path d="M90 62H140M100 95V140M170 80V140M40 235H70M40 170V300M70 290H115M210 240V300M150 330V420H190M270 230V300M230 375V430M75 380V320"/>
    </g>
  </svg>
  <div role="img" aria-label="Collage of member photos linked by dashed lines">
    <div class="collage-photo" style="left:146px;top:55px;width:72px;height:90px"></div>
    <div class="collage-photo" style="left:243px;top:38px;width:64px;height:88px"></div>
    <div class="collage-photo" style="left:312px;top:73px;width:56px;height:72px"></div>
    <div class="collage-photo" style="left:205px;top:118px;width:84px;height:98px"></div>
    <div class="collage-photo" style="left:351px;top:138px;width:70px;height:100px"></div>
    <div class="collage-photo" style="left:120px;top:184px;width:72px;height:96px"></div>
    <div class="collage-photo" style="left:263px;top:196px;width:82px;height:114px"></div>
    <div class="collage-photo" style="left:172px;top:253px;width:66px;height:100px"></div>
    <div class="collage-photo" style="left:329px;top:265px;width:70px;height:100px"></div>
    <div class="collage-photo" style="left:233px;top:317px;width:56px;height:75px"></div>
    <div class="collage-photo" style="left:129px;top:338px;width:76px;height:101px"></div>
    <div class="collage-photo" style="left:275px;top:355px;width:78px;height:102px"></div>
  </div>
  <div class="abs engineer"><b>Engineer</b><span><svg width="7" height="10" viewBox="0 0 7 10"><path d="M3.5 0A3.5 3.5 0 0 1 7 3.5C7 6 3.5 10 3.5 10S0 6 0 3.5A3.5 3.5 0 0 1 3.5 0z" fill="#3aa0e0"/></svg>Singapore</span></div>
  <h1 class="abs hero-title">MEET<br>PEOPLE IN<br>SINGAPORE</h1>
  <div class="abs hero-rule"></div>
  <p class="abs hero-sub">SIGNUP NOW, SHARE YOUR<br>PHOTOS AND THINGS, CREATE<br>YOUR OWN GROUP<br>OR JOIN OTHERS</p>
  <div class="abs btn-try">Try it Yourself</div>
</section>

<section class="abs feature" style="left:83px">
  <div class="feature-head">
    <svg width="22" height="24" viewBox="0 0 22 24"><circle cx="11" cy="6" r="5" fill="#7cbf2a"/><path d="M1 24V17Q1 12 6 12H16Q21 12 21 17V24Z" fill="#7cbf2a"/></svg>
    <h2>Professional Services</h2>
  </div>
  <p>On sait depuis longtemps que travailler avec du texte lisible et contenant du sens.</p>
  <a>GO</a>
</section>
<section class="abs feature" style="left:405px">
  <div class="feature-head">
    <svg width="28" height="26" viewBox="0 0 28 26"><rect x="2" y="5" width="19" height="19" fill="none" stroke="#7cbf2a" stroke-width="3"/><path d="M9 17L12 10L24 1L27 4L15 14Z" fill="#7cbf2a"/></svg>
    <h2>Non-Professionals</h2>
  </div>
  <p>On sait depuis longtemps que travailler avec du texte lisible et contenant du sens.</p>
  <a>GO</a>
</section>
<section class="abs feature" style="left:728px">
  <div class="feature-head">
    <svg width="30" height="26" viewBox="0 0 30 26"><path d="M1 14L5 10L12 17L26 1L29 4L12 24Z" fill="#7cbf2a"/></svg>
    <h2>Selling, helping, lending<br>and borrowing</h2>
  </div>
  <p>On sait depuis longtemps que travailler avec du texte lisible et contenant du sens.</p>
  <a>GO</a>
</section>

<section class="abs band"></section>
<h2 class="abs band-title" style="left:123px;top:832px;color:var(--navy)">QUICK LINKS</h2>
<div class="abs quick-box">
  <article class="post">
    <div class="post-thumb" role="img" aria-label="Member photo" style="background:linear-gradient(#6d6a5a,#3f3b33)"></div>
    <div><h3>Composition et la mise en.</h3><p>Lorem Ipsum est simplement du faux texte employé dans la sition et la misen page avant...</p>
    <div class="post-meta"><span>5 comment <b style="color:#6a9b1e">+</b></span><span>4 July 2012</span></div></div>
  </article>
  <article class="post">
    <div class="post-thumb" role="img" aria-label="Member photo" style="background:linear-gradient(#e2c7a0,#b98a5e)"></div>
    <div><h3>Composition et la mise en.</h3><p>Lorem Ipsum est simplement du faux texte employé dans la sition et la misen page avant...</p>
    <div class="post-meta"><span>5 comment <b style="color:#6a9b1e">+</b></span><span>4 July 2012</span></div></div>
  </article>
</div>
<svg class="abs scrollbar" viewBox="0 0 10 210" aria-hidden="true">
  <circle cx="5" cy="5" r="5" fill="#5a8fd0"/><rect x="3.5" y="26" width="3" height="30" rx="1.5" fill="#5a8fd0"/><circle cx="5" cy="205" r="5" fill="#5a8fd0"/>
</svg>

<h2 class="abs band-title" style="left:429px;top:827px;color:var(--red)">LATEST MEMBERS</h2>
<div role="img" aria-label="Grid of eight recent member photos">
  <div class="member" style="left:431px;top:866px;background:#6f6a3a"></div>
  <div class="member" style="left:503px;top:866px;background:#d8cbbd"></div>
  <div class="member" style="left:574px;top:866px;background:#b98470"></div>
  <div class="member" style="left:645px;top:866px;background:#d9d4cc"></div>
  <div class="member" style="left:431px;top:938px;background:#cfcfcf"></div>
  <div class="member" style="left:503px;top:938px;background:#d5793f"></div>
  <div class="member" style="left:574px;top:938px;background:#2b2b2b"></div>
  <div class="member" style="left:645px;top:938px;background:#8c8c8c"></div>
</div>
<h3 class="abs lorem-head">LOREM IPSUM DOLOR SIT AMET,<br>CONS ECTETUR ADIPSCING ELIT</h3>
<a class="abs show-all">SHOW ALL.</a>

<h2 class="abs band-title" style="left:734px;top:827px;color:var(--green)">JOIN US</h2>
<form class="abs signup">
  <h3>SIGN UP</h3>
  <div class="signup-input">Username</div>
  <div class="signup-input">Password</div>
  <div class="signup-row"><div class="btn-next">Next</div><div class="agree">I Agree <i></i></div></div>
  <div class="signup-links">FORGOT PASSWORD ?<br>RESEND ACTIVATION CODE</div>
</form>

<footer class="abs site-footer">
  <span class="abs" style="left:120px;top:24px">copyright©2013. All Rights Reserved</span>
  <span class="abs" style="left:723px;top:24px">Spread the lanekindred</span>
  <span class="share-btn" style="left:883px">Like</span>
  <span class="share-btn" style="left:932px">Share</span>
  <span class="share-btn" style="left:972px">Post</span>
</footer>

</body>
</html>
```